The Wager a non-fiction book on mindfulness COVER design needed

A non-fiction book about active mindfulness.
The Wager includes 21 different daily 'dares' which are action based activities to generate positive mindfulness - to become more contented with life.
Based on the teeaching of the New Thought movements of the early 20th century, think The Hidden Key, Plan and Become Wealthy.
The book is positive and uplifting. It fits into the self-help / spiritual / health segments. It skews female 40 to 50 year olds.
Think fresh colours like a bold orange or bright green.
What needs to be on the cover:
TITLE: The Wager
AUTHOR: Martin Fenwick
BLURB: Get clarity, focus, and a new zest for life by following The Wager for just 21 days.
Women 40-50 english speaking
Self-help / Health

```html
<!DOCTYPE html>
<html lang="en">
<head>
<meta charset="utf-8">
<title>The Wager — Book Cover</title>
<link rel="stylesheet" href="https://fonts.googleapis.com/css2?family=Bebas+Neue&display=swap">
<style>
  :root {
    --stage: #e9e6e1;
    --cover-orange: #ef5a24;
    --accent-yellow: #f5e933;
    --title-white: #ffffff;
  }
  * { margin: 0; padding: 0; box-sizing: border-box; }
  html, body {
    width: 1200px;
    height: 1000px;
    overflow: hidden;
    background: var(--stage);
  }
  .canvas {
    position: relative;
    width: 1200px;
    height: 1000px;
    background: var(--stage);
  }
  .cover {
    position: absolute;
    left: 270px;
    top: 20px;
    width: 660px;
    height: 960px;
    background: var(--cover-orange);
    overflow: hidden;
    font-family: "Bebas Neue", "Arial Narrow", sans-serif;
  }
  .author {
    position: absolute;
    left: 70px;
    top: 58px;
    font-size: 50px;
    line-height: 1;
    letter-spacing: 0.14em;
    color: var(--accent-yellow);
    white-space: nowrap;
  }
  .rule {
    position: absolute;
    width: 19px;
  }
  .rule--top {
    left: 492px;
    top: 0;
    height: 262px;
    background: var(--title-white);
  }
  .rule--bottom {
    left: 356px;
    top: 430px;
    bottom: 0;
    background: var(--accent-yellow);
  }
  .title {
    position: absolute;
    right: 8px;
    white-space: nowrap;
    line-height: 1;
  }
  .title__article {
    top: 236px;
    font-size: 206px;
    color: var(--title-white);
  }
  .title__word {
    top: 398px;
    font-size: 272px;
    letter-spacing: -0.01em;
    color: var(--accent-yellow);
  }
  .blurb {
    position: absolute;
    left: 414px;
    top: 664px;
    font-size: 31px;
    line-height: 1.33;
    letter-spacing: 0.02em;
    color: var(--title-white);
  }
  .blurb .highlight { color: var(--accent-yellow); }
</style>
</head>
<body>
  <main class="canvas">
    <section class="cover" aria-label="Book cover: The Wager by Martin Fenwick">
      <div class="author">Martin Fenwick</div>
      <div class="rule rule--top"></div>
      <div class="rule rule--bottom"></div>
      <h1>
        <span class="title title__article">THE</span>
        <span class="title title__word">WAGER</span>
      </h1>
      <p class="blurb">
        GET CLARITY<span class="highlight">,</span><br>
        FOCUS<span class="highlight">,</span> AND<br>
        A NEW ZEST<br>
        FOR LIFE<br>
        BY FOLLOWING<br>
        <span class="highlight">THE WAGER</span><br>
        FOR JUST 21 DAYS
      </p>
    </section>
  </main>
</body>
</html>
```